New Business Card Design Project LORVANTI-Italy

we are LORVANTI-Italy
our company in the market for 3 years we are luxury cosmetic company and its about time for a facelift :)
i will like to have elegant luxurious and unique business card
that will give the person that get it a unique, luxurious and elegant impression
I'm VERY OPEN FOR NEW IDEAS , even duo i add a few files of things that i see on line and i like them

i add my logo as well
my website is LORVANTI.COM
(if you would like to see the main style that we have)

Target Market(s)

adult that have money :)

Industry/Entity Type

Business

Contact Information for Business Card

Name - Dario Lorvanti
Position - CEO and CO Founder
address - 4817 E Halvern
telephone - 555-384-1926
email - dario@lorvanti.com
fax - 555-384-1926
website - LORVANTI.COM

Colors
000000
959595
fbee3e
ffffff

Requirements
Must have
• big logo in GOLD color
• elegant look
• impressive
Nice to have
• not must but maybe classy pattern background
• not must but maybe emblem
• maybe clear plastic business card
Should not have
• colors
• images

```html
<!DOCTYPE html>
<html lang="en">
<head>
<meta charset="utf-8">
<title>LORVANTI Italy — Business Card</title>
<link rel="stylesheet" href="https://fonts.googleapis.com/css2?family=Open+Sans:wght@400;600&display=swap">
<style>
  :root {
    --stage: #2a2a2b;
    --card: #0e0e0f;
    --card-edge: #1c1c1d;
    --pattern-dark: #141415;
    --pattern-light: #262627;
    --gold: #d9ad35;
  }
  * { margin: 0; padding: 0; box-sizing: border-box; }
  html, body { width: 1200px; height: 1200px; overflow: hidden; }
  body {
    background: var(--stage);
    font-family: "Open Sans", Arial, sans-serif;
    color: var(--gold);
    position: relative;
  }
  .card {
    position: absolute;
    left: 180px;
    width: 840px;
    height: 480px;
    border-radius: 14px;
    background: var(--card);
    overflow: hidden;
    box-shadow: 0 18px 40px rgba(0,0,0,0.55);
  }
  .card--front { top: 90px; }
  .card--back { top: 630px; }
  .card__pattern {
    position: absolute;
    inset: 0;
    width: 100%;
    height: 100%;
  }
  .brand {
    position: absolute;
    display: flex;
    flex-direction: column;
    align-items: center;
  }
  .brand__mark {
    border-radius: 50%;
    border: 4px solid var(--gold);
  }
  .brand__name {
    color: var(--gold);
    font-weight: 400;
    letter-spacing: 0.04em;
    line-height: 1;
  }
  .brand__rule {
    background: var(--gold);
    height: 3px;
  }
  .card--front .brand { left: 0; right: 0; top: 70px; }
  .card--front .brand__mark { width: 180px; height: 180px; }
  .card--front .brand__name { font-size: 78px; margin-top: 34px; }
  .card--front .brand__rule { width: 420px; margin-top: 14px; }

  .card--back .brand { right: 70px; top: 150px; width: 300px; }
  .card--back .brand__mark { width: 130px; height: 130px; border-width: 3px; }
  .card--back .brand__name { font-size: 50px; margin-top: 26px; }
  .card--back .brand__rule { width: 270px; height: 2px; margin-top: 10px; }

  .contact {
    position: absolute;
    left: 96px;
    top: 62px;
  }
  .contact__name { font-size: 38px; font-weight: 400; line-height: 1.1; }
  .contact__role { font-size: 20px; margin-top: 6px; }
  .contact__list { list-style: none; margin-top: 34px; }
  .contact__item {
    display: flex;
    align-items: center;
    gap: 16px;
    font-size: 18px;
    height: 50px;
  }
  .contact__icon { width: 30px; height: 30px; flex: none; }
</style>
</head>
<body>

<section class="card card--front" aria-label="Card front">
  <svg class="card__pattern" viewBox="0 0 840 480" role="img" aria-label="Dark damask pattern with a large lattice arc ornament on the left">
    <defs>
      <radialGradient id="front-tone" cx="0.15" cy="0.5" r="0.7">
        <stop offset="0" stop-color="#262627"/>
        <stop offset="1" stop-color="#0e0e0f"/>
      </radialGradient>
    </defs>
    <rect width="840" height="480" fill="url(#front-tone)"/>
  </svg>
  <div class="brand">
    <div class="brand__mark"></div>
    <div class="brand__name">LORVANTI</div>
    <div class="brand__rule"></div>
  </div>
</section>

<section class="card card--back" aria-label="Card back">
  <svg class="card__pattern" viewBox="0 0 840 480" role="img" aria-label="Dark damask pattern with a large lattice arc ornament on the right">
    <defs>
      <radialGradient id="back-tone" cx="0.82" cy="0.6" r="0.6">
        <stop offset="0" stop-color="#262627"/>
        <stop offset="1" stop-color="#0e0e0f"/>
      </radialGradient>
    </defs>
    <rect width="840" height="480" fill="url(#back-tone)"/>
  </svg>

  <div class="contact">
    <h1 class="contact__name">Dario Lorvanti</h1>
    <p class="contact__role">CEO and CO Founder</p>
    <ul class="contact__list">
      <li class="contact__item">
        <svg class="contact__icon" viewBox="0 0 30 30" fill="none" stroke="currentColor" stroke-width="1.6"><circle cx="15" cy="15" r="13.5"/><path d="M15 23s-5-5.5-5-9a5 5 0 0 1 10 0c0 3.5-5 9-5 9z"/><circle cx="15" cy="14" r="1.8"/></svg>
        4817 E Halvern
      </li>
      <li class="contact__item">
        <svg class="contact__icon" viewBox="0 0 30 30" fill="none" stroke="currentColor" stroke-width="1.6"><circle cx="15" cy="15" r="13.5"/><path d="M10 9l3 0 1.5 3.5-2 1.5a8 8 0 0 0 3.5 3.5l1.5-2 3.5 1.5v3c-6 1-12-5-11-11z"/></svg>
        555-384-1926
      </li>
      <li class="contact__item">
        <svg class="contact__icon" viewBox="0 0 30 30" fill="none" stroke="currentColor" stroke-width="1.6"><circle cx="15" cy="15" r="13.5"/><rect x="8.5" y="10" width="13" height="10" rx="1"/><path d="M8.5 10.5l6.5 5 6.5-5"/></svg>
        dario@lorvanti.com
      </li>
      <li class="contact__item">
        <svg class="contact__icon" viewBox="0 0 30 30" fill="none" stroke="currentColor" stroke-width="1.6"><circle cx="15" cy="15" r="13.5"/><rect x="8" y="13" width="14" height="7" rx="1"/><path d="M11 13V8.5h8V13M11 17h8"/></svg>
        555-384-1926
      </li>
      <li class="contact__item">
        <svg class="contact__icon" viewBox="0 0 30 30" fill="none" stroke="currentColor" stroke-width="1.6"><circle cx="15" cy="15" r="13.5"/><circle cx="15" cy="15" r="7"/><path d="M8 15h14M15 8c-3 4-3 10 0 14M15 8c3 4 3 10 0 14"/></svg>
        lorvanti.com
      </li>
    </ul>
  </div>

  <div class="brand">
    <div class="brand__mark"></div>
    <div class="brand__name">LORVANTI</div>
    <div class="brand__rule"></div>
  </div>
</section>

</body>
</html>
```